Design a WordPress layout for a home loans company

The home loans company in question is going through a rebrand and needs a new website layout.
Sites they like: http://www.brightkeylending.com.au/
Current logo: Attached.
Colours to be used: As per those used in logo.
Primary: #71aa3d
Secondary: #130e10
Pages to be designed:
- Homepage
- Internal services page
Menu items for display purposes:
- Home
- About Us
- Speak to a Broker
- Articles
- Contact Us
A modern design with simplicity is key.
For copy, dummy text such as Lorem ipsum will be fine.
If you would like anything elso, please ask.
Target Market(s)
25-40 year old
Mostly female
Buying their first home in most cases
Industry/Entity Type
Mortgage Brokerage
Number of Pages Required
2 page

```html
<!DOCTYPE html>
<html lang="en">
<head>
<meta charset="utf-8">
<title>Northgate Home Loans</title>
<link href="https://fonts.googleapis.com/css2?family=Montserrat:wght@400;500;700;800&family=Open+Sans:wght@400;600&display=swap" rel="stylesheet">
<style>
:root{
  --green:#71aa3d;
  --green-dark:#5a9a2c;
  --ink:#130e10;
  --text:#444;
  --muted:#777;
  --white:#fff;
  --line:#e3e3e3;
  --footer:#ececec;
  --footer-bar:#d6d6d6;
}
*{margin:0;padding:0;box-sizing:border-box}
html,body{width:1200px;height:2880px;overflow:hidden}
body{position:relative;background:var(--white);font-family:"Open Sans",Arial,sans-serif;color:var(--text)}
.abs{position:absolute}
/* top bar */
.topbar{left:0;top:0;width:1200px;height:27px;background:var(--green);color:var(--white);font-size:13px}
.topbar .item{position:absolute;top:5px;display:flex;align-items:center;gap:6px}
/* header */
.header{left:0;top:27px;width:1200px;height:96px;background:var(--white)}
.brand{position:absolute;left:184px;top:22px;display:flex;align-items:center;gap:10px;font-family:"Montserrat",sans-serif;font-weight:700;font-size:21px;line-height:25px;color:var(--green);white-space:nowrap}
.brand .mark{width:16px;height:16px;background:var(--green);flex:none}
.nav{position:absolute;left:0;top:44px;width:1200px;height:20px;font-family:"Montserrat",sans-serif;font-size:13px;font-weight:500;color:var(--ink)}
.nav span{position:absolute;top:0;white-space:nowrap}
.nav .active{color:var(--green)}
/* hero */
.hero{left:0;top:123px;width:1200px;height:503px;background:linear-gradient(180deg,#ececec 0%,#e2e2e2 78%,#cfcfcf 100%)}
.hero-photo{position:absolute;left:520px;top:0;width:680px;height:503px;background:radial-gradient(ellipse at 55% 55%,#d7c3b5 0%,#c9c2bf 35%,rgba(226,226,226,0) 70%)}
.hero h1{position:absolute;left:186px;top:112px;font-family:"Montserrat",sans-serif;font-weight:800;font-size:40px;line-height:46px;color:var(--ink)}
.hero h1 em{font-style:normal;color:var(--green)}
.hero p{position:absolute;left:188px;top:215px;width:340px;font-size:14px;line-height:21px;color:#555}
.btn{position:absolute;display:flex;align-items:center;justify-content:center;font-family:"Montserrat",sans-serif;font-weight:700;font-size:14px;color:var(--white)}
.btn-green{background:linear-gradient(180deg,#7cb648,#5c962c)}
.btn-dark{background:var(--ink)}
.dots{position:absolute;left:192px;top:358px;display:flex;align-items:center;gap:6px}
.dots i{width:7px;height:7px;border-radius:50%;background:#bbb;display:block}
/* about */
.section-title{position:absolute;left:0;width:1200px;text-align:center;font-family:"Montserrat",sans-serif;font-weight:400;font-size:30px;color:var(--ink)}
.about-copy{position:absolute;left:255px;top:736px;width:690px;text-align:center;font-size:15px;line-height:21px;color:#555}
.card{position:absolute;top:860px;width:254px;height:190px;border:2px solid #a8d07f;background:#f7f7f7;text-align:center}
.card svg{margin-top:20px}
.card h3{font-family:"Open Sans",sans-serif;font-weight:400;font-size:18px;color:var(--ink);margin-top:10px}
.card p{font-size:11px;line-height:15px;color:#777;padding:6px 34px 0}
.card a{display:block;margin-top:10px;font-size:12px;font-weight:600;color:var(--green);text-decoration:none}
/* broker */
.broker-copy{position:absolute;left:624px;top:1220px;width:370px;color:var(--white)}
.broker-copy h2{font-family:"Montserrat",sans-serif;font-weight:400;font-size:30px}
.broker-copy p{margin-top:20px;font-size:14px;line-height:22px}
.btn-outline{border:2px solid var(--white);background:transparent}
/* articles */
.article{position:absolute;top:1726px;width:409px;height:310px;border:1px solid #ccc;background:var(--white)}
.article .photo{width:100%;height:198px}
.article h3{font-family:"Open Sans",sans-serif;font-weight:400;font-size:17px;color:var(--ink);margin:14px 0 0 30px}
.article p{font-size:11px;line-height:15px;color:#777;margin:6px 30px 0}
.article a{display:block;margin:6px 0 0 30px;font-size:12px;font-weight:600;color:var(--green);text-decoration:none}
/* contact */
.contact{left:0;top:2097px;width:1200px;height:453px;background:linear-gradient(90deg,#3a3735,#4a4642 45%,#2f2d2b)}
.contact h2{position:absolute;left:0;top:100px;width:1200px;text-align:center;font-family:"Montserrat",sans-serif;font-weight:400;font-size:30px;color:var(--white)}
.contact .sub{position:absolute;left:0;top:142px;width:1200px;text-align:center;font-size:16px;color:#ddd}
.field{position:absolute;width:280px;height:36px;border-bottom:1px solid #ccc;color:var(--white);font-size:15px;padding-top:6px}
/* footer */
.footer{left:0;top:2550px;width:1200px;height:272px;background:var(--footer)}
.footer .brand{left:184px;top:74px;font-size:21px}
.fcol{position:absolute;top:52px;font-size:12px;line-height:23px;color:#444}
.fcol h4{font-family:"Open Sans",sans-serif;font-weight:400;font-size:14px;color:var(--green);margin-bottom:8px}
.fcol .row{display:flex;gap:8px;align-items:flex-start}
.social{display:flex;gap:6px}
.social i{display:block;width:34px;height:34px;border:2px solid var(--ink);border-radius:50%}
.bottombar{left:0;top:2822px;width:1200px;height:58px;background:var(--footer-bar);text-align:center;font-size:12px;color:#444;padding-top:20px}
</style>
</head>
<body>

<div class="abs topbar">
  <div class="item" style="left:678px">
    <svg width="12" height="10" viewBox="0 0 12 10"><rect x="0.5" y="0.5" width="11" height="9" fill="none" stroke="#fff"/><path d="M0.5 0.5 6 5.5 11.5 0.5" fill="none" stroke="#fff"/></svg>
    hello@northgateloans.example
  </div>
  <div class="item" style="left:898px">
    <svg width="12" height="12" viewBox="0 0 12 12"><path d="M2 1 4.5 1 5.5 4 4 5.2Q5.5 7.8 7 8.5L8.2 7 11 8v2.5Q9.5 12 6 10 1.5 7 0.8 2.5Z" fill="#fff"/></svg>
    (08) 9000 4100
  </div>
</div>

<header class="abs header">
  <div class="brand"><span class="mark"></span><span>Northgate<br>Home Loans</span></div>
  <nav class="nav">
    <span class="active" style="left:510px">HOME</span>
    <span style="left:584px">ABOUT US</span>
    <span style="left:682px">SPEAK TO BROKER</span>
    <span style="left:838px">ARTICLES</span>
    <span style="left:934px">CONTACT US</span>
  </nav>
</header>

<section class="abs hero">
  <div class="hero-photo" role="img" aria-label="Photo of a young family sitting on the floor under a cardboard roof against a white brick wall"></div>
  <h1>GET FAST &amp; EASY<br><em>HOME LOANS</em></h1>
  <p>Aptent taciti sociosqu ad litora torquent per conubia nostra per inceptos hymenaeos Proin nulla</p>
  <div class="btn btn-green" style="left:186px;top:284px;width:160px;height:40px">GET HOME LOAN</div>
  <div class="btn btn-dark" style="left:351px;top:284px;width:162px;height:40px">CONATCT US</div>
  <div class="dots"><svg width="16" height="16"><circle cx="8" cy="8" r="7" fill="#999"/><path d="M9.5 4.5 6 8l3.5 3.5" stroke="#fff" stroke-width="1.5" fill="none"/></svg><i></i><i></i><i></i><i></i><svg width="16" height="16"><circle cx="8" cy="8" r="7" fill="#999"/><path d="M6.5 4.5 10 8l-3.5 3.5" stroke="#fff" stroke-width="1.5" fill="none"/></svg></div>
</section>

<svg class="abs" style="left:580px;top:648px" width="40" height="36" viewBox="0 0 40 36"><path d="M4 18 20 3 36 18" fill="none" stroke="#71aa3d" stroke-width="3"/><path d="M10 14v20h20V14" fill="none" stroke="#71aa3d" stroke-width="3"/><path d="M20 32V16m-5 5 5-5 5 5" fill="none" stroke="#71aa3d" stroke-width="2.5"/></svg>
<h2 class="section-title" style="top:688px">ABOUT NORTHGATE HOME LOANS</h2>
<p class="about-copy">Maecenas aliquet velit vel turpis Mauris neque metus malesuada nec ultricies sit amet porttitor mattis enim In massa libero interdum nec interdum vel blandit sed nulla In ullamcorper est eget tempor cursus neque mi consectetuer mi a ultricies massa est sed nisl</p>

<div class="card" style="left:196px">
  <svg width="46" height="48" viewBox="0 0 46 48"><path d="M12 44V34Q4 28 6 17 9 5 22 4 36 4 38 17l4 8h-4v8q0 4-6 4h-4v7" fill="none" stroke="#71aa3d" stroke-width="2"/><circle cx="22" cy="18" r="7" fill="none" stroke="#333" stroke-width="2"/><path d="M20 25v4h4v-4" fill="none" stroke="#333" stroke-width="2"/></svg>
  <h3>Trusted Advice</h3>
  <p>Anec interdum vel blandit sed nulla In ullamcorper est eget tempor</p>
  <a>Click here</a>
</div>
<div class="card" style="left:465px">
  <svg width="50" height="48" viewBox="0 0 50 48"><rect x="4" y="12" width="42" height="32" fill="none" stroke="#333" stroke-width="2"/><path d="M17 12V5h16v7" fill="none" stroke="#333" stroke-width="2"/><path d="M4 22h42" stroke="#71aa3d" stroke-width="2"/><circle cx="32" cy="30" r="5" fill="none" stroke="#71aa3d" stroke-width="2"/><path d="M24 42q8-10 16 0" fill="none" stroke="#71aa3d" stroke-width="2"/></svg>
  <h3>Find a Broker</h3>
  <p>Anec interdum vel blandit sed nulla In ullamcorper est eget tempor</p>
  <a>Click here</a>
</div>
<div class="card" style="left:733px">
  <svg width="50" height="48" viewBox="0 0 50 48"><path d="M10 20 25 6 40 20" fill="none" stroke="#71aa3d" stroke-width="2"/><rect x="15" y="18" width="20" height="16" fill="none" stroke="#71aa3d" stroke-width="2"/><path d="M4 40q10-6 20-2h12l10-6" fill="none" stroke="#333" stroke-width="2"/></svg>
  <h3>How to get loan</h3>
  <p>Anec interdum vel blandit sed nulla In ullamcorper est eget tempor</p>
  <a>Click here</a>
</div>

<svg class="abs" style="left:0;top:1085px" width="1200" height="560" viewBox="0 0 1200 560">
  <polygon points="0,0 140,28 0,28" fill="#9a9a9a"/>
  <polygon points="0,22 1200,0 1200,556 0,556" fill="#5c9a2e"/>
  <polygon points="0,22 1200,0 1200,520 860,510 0,556" fill="#5f9c30"/>
  <polygon points="0,470 900,510 1200,550 1200,560 0,560" fill="#fff"/>
  <polygon points="860,512 1200,495 1200,560" fill="#111"/>
  <polygon points="1000,506 1200,495 1200,515" fill="#8a8a8a"/>
</svg>
<div class="abs" style="left:0;top:1110px;width:620px;height:532px;background:linear-gradient(90deg,#8d8f96 0%,#a89a90 45%,rgba(95,156,48,0.6) 85%,rgba(95,156,48,0) 100%);clip-path:polygon(0 0,100% 0,100% 95%,0 100%)" role="img" aria-label="Photo of a smiling young couple reviewing loan papers with a broker, a small model house on the desk"></div>
<div class="broker-copy">
  <h2>SPEAK TO BROKER</h2>
  <p>Maecenas aliquet velit vel turpis Mauris neque metus malesuada nec ultricies sit amet porttitor libero interdum nec interdum vel blandit sed nulla In ullamcorper est eget tempor cursus neque mi consectetuer mi a ultricies massa est sed nisl</p>
</div>
<div class="btn btn-outline" style="left:626px;top:1417px;width:160px;height:40px">LEARN MORE</div>

<h2 class="section-title" style="top:1670px;font-size:27px">ARTICLES &amp; BLOGS</h2>
<svg class="abs" style="left:132px;top:1846px" width="20" height="50"><path d="M17 2 3 25l14 23" fill="none" stroke="#666" stroke-width="2"/></svg>
<svg class="abs" style="left:1036px;top:1846px" width="20" height="50"><path d="M3 2l14 23L3 48" fill="none" stroke="#666" stroke-width="2"/></svg>
<div class="article" style="left:179px">
  <div class="photo" style="background:linear-gradient(135deg,#6e8a2e,#c99a4a 55%,#8a6a2a)" role="img" aria-label="Photo of two hands holding a small model house and a money bag outdoors"></div>
  <h3>Etiam est nunc venenatis tristique</h3>
  <p>netus et malesuada fames ac turpis egestas Cras id elit Integer quis urna Ut ante enim dapibus malesuada fringilla eu condimen</p>
  <a>READ MORE</a>
</div>
<div class="article" style="left:607px">
  <div class="photo" style="background:linear-gradient(90deg,#c8323a 0%,#d9c9c4 45%,#e8e6e4 60%,#1e2a44 100%)" role="img" aria-label="Photo of a woman in red shaking hands with a man in a suit across a desk"></div>
  <h3>Etiam est nunc venenatis tristique</h3>
  <p>netus et malesuada fames ac turpis egestas Cras id elit Integer quis urna Ut ante enim dapibus malesuada fringilla eu condimen</p>
  <a>READ MORE</a>
</div>

<section class="abs contact" role="img" aria-label="Darkened photo of a family relaxing together on a sofa in a living room">
  <svg style="position:absolute;left:0;top:0" width="1200" height="40"><polygon points="0,0 1200,0 1200,0 0,40" fill="#fff"/><polygon points="0,30 260,4 0,40" fill="#5f9c30"/><polygon points="0,12 120,4 0,30" fill="#8a8a8a"/></svg>
  <h2>CONTACT US NOW</h2>
  <div class="sub">Maecenas aliquet velit vel turpis Mauris neque metus</div>
  <div class="field" style="left:311px;top:202px">Full Name</div>
  <div class="field" style="left:614px;top:202px">Email address</div>
  <div class="field" style="left:311px;top:259px">Phone</div>
  <div class="field" style="left:614px;top:259px">City</div>
  <div class="btn btn-green" style="left:532px;top:315px;width:150px;height:36px">SUBMIT</div>
</section>

<footer class="abs footer">
  <div class="brand"><span class="mark"></span><span>Northgate<br>Home Loans</span></div>
  <div class="fcol" style="left:402px"><h4>QUICK LINKS</h4>Home<br>About us<br>Speak to Broker<br>Articles<br>Contact us</div>
  <div class="fcol" style="left:542px"><h4>RESOURCES</h4>Testimonials<br>Privacy Policy<br>Sitemap<br>FAQ</div>
  <div class="fcol" style="left:682px;width:190px">
    <h4>CONTACT US</h4>
    <div class="row"><svg width="10" height="14" style="margin-top:5px"><path d="M5 14C1 8 0 6 0 5a5 5 0 0 1 10 0c0 1-1 3-5 9z" fill="#333"/><circle cx="5" cy="5" r="2" fill="#ececec"/></svg><span>18 Harbour Rd Parkside,<br>Western Australia</span></div>
    <div class="row"><svg width="10" height="12" style="margin-top:6px"><path d="M2 1h2l1 3-1.5 1Q5 8 6.5 8.5L8 7l2 1v2.5Q8 12 5 10 1 7 .5 2.5Z" fill="#333"/></svg><span>(08) 9000 4100</span></div>
    <div class="row"><svg width="12" height="10" style="margin-top:7px"><rect width="12" height="9" fill="#333"/><path d="M0 0 6 5 12 0" fill="none" stroke="#ececec"/></svg><span>hello@northgateloans.example</span></div>
  </div>
  <div class="fcol" style="left:874px"><h4>FOLLOW US</h4><div class="social"><i></i><i></i><i></i><i></i></div></div>
</footer>
<div class="abs bottombar">© 2018 Company Name All right reserved</div>

</body>
</html>
```